Business Card Design

Tumble Harbor is a Laundromat Store
we provide wash and Fold service to Customers who are busy with their life and can not come to the store and do laundry
we have customers who drop their laundry at the store
but now i want to provide service to customers who are not able to come to the store to drop. i will go to their address and pickup the laundry and get it washed folded and delivered
Updates
Can you use the colour in you design which i uploaded and also fusha fluorescent green bright pink
Target Market(s)
all works of life who don't have time to do laundry
Industry/Entity Type
Store
Contact Information for Business Card
TumbleHarbor Laundromat
247 Mallory Street
Lynn MA 01938
Look and feel
Each slider illustrates characteristics of the customer's brand and the style your logo design should communicate.

```html
<!DOCTYPE html>
<html lang="en">
<head>
<meta charset="UTF-8">
<title>TumbleHarbor Laundromat – Business Card</title>
<link rel="stylesheet" href="https://fonts.googleapis.com/css2?family=Lato:wght@300;400;700;900&display=swap">
<style>
  :root {
    --stage: #2f2f2f;
    --card-pink: #ec1a8c;
    --band-top: #b8188a;
    --band-bottom: #7c1a6e;
    --call-box: #6a1f5e;
    --badge: #9a2b8c;
    --badge-ring: #c45bb3;
    --white: #ffffff;
    --pile-a: #c9a9c4;
    --pile-b: #8f6f9a;
    --stack-a: #b05a8c;
    --stack-b: #4f5f7d;
  }
  html, body {
    margin: 0;
    width: 1200px;
    height: 900px;
    overflow: hidden;
    background: var(--stage);
    font-family: "Lato", Arial, sans-serif;
  }
  .card {
    position: absolute;
    left: 40px;
    top: 130px;
    width: 1120px;
    height: 640px;
    background: var(--card-pink);
    overflow: hidden;
    color: var(--white);
  }
  .card-art { position: absolute; inset: 0; }
  .brand-name {
    position: absolute;
    top: 42px;
    left: 0;
    width: 100%;
    margin: 0;
    text-align: center;
    font-size: 50px;
    font-weight: 400;
    letter-spacing: 0.5px;
  }
  .brand-name strong { font-weight: 700; }
  .address {
    position: absolute;
    top: 112px;
    left: 0;
    width: 100%;
    margin: 0;
    text-align: center;
    font-size: 25px;
    font-weight: 700;
    letter-spacing: 6px;
    text-transform: uppercase;
  }
  .call-us {
    position: absolute;
    top: 160px;
    left: 50%;
    transform: translateX(-50%);
    background: var(--call-box);
    padding: 8px 16px;
    font-size: 26px;
    font-weight: 700;
    white-space: nowrap;
  }
  .call-us .number { font-weight: 900; margin-left: 6px; }
  .photo {
    position: absolute;
    border-radius: 14px;
  }
  .photo-pile {
    left: 250px; top: 228px; width: 210px; height: 150px;
    background: radial-gradient(circle at 50% 55%, var(--pile-a), var(--pile-b));
    border-radius: 50% 50% 30% 30%;
  }
  .photo-stack {
    left: 650px; top: 222px; width: 195px; height: 160px;
    background: linear-gradient(180deg, var(--stack-a), var(--stack-b));
    border-radius: 18px;
  }
  .from-to {
    position: absolute;
    left: 478px; top: 216px;
    width: 156px; height: 156px;
    border-radius: 50%;
    background: var(--badge);
    box-shadow: 0 0 0 5px var(--badge-ring);
    text-align: center;
  }
  .from-to .from {
    position: absolute; top: 34px; left: 0; width: 100%;
    font-size: 32px; font-weight: 400; letter-spacing: 1px;
  }
  .from-to .to {
    position: absolute; top: 86px; left: 0; width: 100%;
    font-size: 32px; font-weight: 700;
  }
  .step {
    position: absolute;
    width: 240px;
    text-align: center;
  }
  .step-icon {
    width: 110px; height: 110px;
    margin: 0 auto;
    border-radius: 50%;
    background: var(--white);
    box-shadow: 0 3px 10px rgba(0,0,0,0.3);
    display: flex; align-items: center; justify-content: center;
  }
  .step-icon .icon-fill {
    width: 74px; height: 74px;
    border-radius: 50%;
  }
  .step-label {
    margin: 18px 0 0;
    font-size: 22px;
    font-weight: 700;
    line-height: 1.2;
  }
  .step-schedule { left: 80px;  top: 440px; }
  .step-pickup   { left: 340px; top: 410px; }
  .step-wash     { left: 600px; top: 392px; }
  .step-enjoy    { left: 860px; top: 378px; }
  .step-schedule .icon-fill { background: linear-gradient(#ffffff, #9a9a9a); }
  .step-pickup .icon-fill   { background: linear-gradient(#4aa3df, #e0773a); }
  .step-wash .icon-fill     { background: linear-gradient(#9aa3ad, #3e4752); }
  .step-enjoy .icon-fill    { background: radial-gradient(circle, #ffe54d, #f0a818); }
</style>
</head>
<body>
  <section class="card">
    <svg class="card-art" width="1120" height="640" viewBox="0 0 1120 640" aria-hidden="true">
      <defs>
        <linearGradient id="bandGrad" x1="0" y1="0" x2="0" y2="1">
          <stop offset="0" stop-color="#b8188a"/>
          <stop offset="1" stop-color="#7c1a6e"/>
        </linearGradient>
      </defs>
      <path d="M0 470 Q560 300 1120 400 L1120 640 L0 640 Z" fill="url(#bandGrad)"/>
      <g fill="none" stroke="#ffffff" stroke-width="3" stroke-linecap="round">
        <path d="M268 500 Q320 470 372 486"/>
        <path d="M362 478 L374 486 L362 494"/>
        <path d="M528 468 Q580 440 632 452"/>
        <path d="M622 444 L634 452 L622 460"/>
        <path d="M788 446 Q840 418 892 432"/>
        <path d="M882 424 L894 432 L882 440"/>
      </g>
    </svg>

    <h1 class="brand-name"><strong>TumbleHarbor</strong> LAUNDROMAT</h1>
    <p class="address">247 Mallory Street Lynn MA 01938</p>
    <div class="call-us">CALL US: <span class="number">079 512 60384</span></div>

    <div class="photo photo-pile" role="img" aria-label="Photo of a pile of crumpled dirty laundry"></div>
    <div class="from-to">
      <span class="from">FROM</span>
      <svg width="156" height="156" viewBox="0 0 156 156" style="position:absolute;left:0;top:0" aria-hidden="true">
        <g stroke="#ffffff" stroke-width="2" fill="none" stroke-linecap="round">
          <path d="M34 78 H122"/><path d="M116 72 L122 78 L116 84"/>
        </g>
      </svg>
      <span class="to">TO</span>
    </div>
    <div class="photo photo-stack" role="img" aria-label="Photo of a neat stack of folded clean clothes"></div>

    <div class="step step-schedule">
      <div class="step-icon"><div class="icon-fill" role="img" aria-label="Illustration of a schedule calendar"></div></div>
      <p class="step-label">You Schedule<br>A Pick-Up</p>
    </div>
    <div class="step step-pickup">
      <div class="step-icon"><div class="icon-fill" role="img" aria-label="Illustration of a house"></div></div>
      <p class="step-label">We Pick-Up<br>Your Dirty Laundry</p>
    </div>
    <div class="step step-wash">
      <div class="step-icon"><div class="icon-fill" role="img" aria-label="Illustration of washing machines"></div></div>
      <p class="step-label">We Wash, Dry, Fold<br>&amp; Return Clean Laundry</p>
    </div>
    <div class="step step-enjoy">
      <div class="step-icon"><div class="icon-fill" role="img" aria-label="Illustration of a happy character giving a thumbs up"></div></div>
      <p class="step-label">Enjoy Effortless<br>Clean Laundry</p>
    </div>
  </section>
</body>
</html>
```